Oil Field Service company needs professional business cards

Looking to clean up our current company business cards and look a little more professional. Brenwick Casing Services is a US based company that services the oil field. We deal with engineers, managers and oil rigs....................................................................................................................................................................................................................................................................................................................................................................................................

Target Market(s)

Oil and Gas professionals

Industry/Entity Type

Oil And Gas

Contact Information for Business Card

See attached photo as example

Font styles to use
Sans Serif

Colors
ec1f27

Requirements
Must have
• Company Logo, Name, Title, Cell, Office, Fax, Email.
• See attached photo
Nice to have
• External CRT, Internal CRT, Casing Crews, Torque Turn, Laydown Machine
Should not have
• Do not introduce any new pictures and keep it professional looking

```html
<!DOCTYPE html>
<html lang="en">
<head>
<meta charset="utf-8">
<title>Brenwick Casing Services – Business Cards</title>
<link href="https://fonts.googleapis.com/css2?family=Open+Sans:wght@400;600;700;800&family=Roboto+Condensed:wght@400;700&display=swap" rel="stylesheet">
<style>
  :root {
    --slate: #4a535c;
    --slate-dark: #3f474f;
    --red: #ec1f27;
    --white: #ffffff;
    --paper: #e9eaec;
    --ink-soft: #dfe3e6;
  }
  html, body {
    margin: 0;
    padding: 0;
    width: 1200px;
    height: 950px;
    overflow: hidden;
    background: var(--paper);
  }
  .canvas {
    width: 1200px;
    height: 950px;
    display: flex;
    flex-direction: column;
    align-items: center;
    justify-content: center;
    gap: 26px;
  }
  .card {
    width: 770px;
    height: 440px;
    display: block;
    box-shadow: 0 6px 18px rgba(0,0,0,0.18);
  }
  .brand-name { font-family: "Open Sans", sans-serif; font-weight: 800; }
  .brand-tag { font-family: "Open Sans", sans-serif; font-weight: 800; letter-spacing: 6px; }
  .services { font-family: "Roboto Condensed", sans-serif; font-weight: 700; font-size: 17px; fill: var(--white); letter-spacing: 0.5px; }
  .person-name { font-family: "Roboto Condensed", sans-serif; font-weight: 700; font-size: 30px; fill: var(--red); letter-spacing: 0.5px; }
  .person-title { font-family: "Open Sans", sans-serif; font-weight: 700; font-size: 20px; fill: var(--white); }
  .contact { font-family: "Open Sans", sans-serif; font-weight: 400; font-size: 19px; fill: var(--ink-soft); }
  .contact-strong { font-weight: 700; fill: var(--white); }
  .icon { fill: var(--red); }
  .icon-line { fill: none; stroke: var(--red); stroke-width: 2; }
</style>
</head>
<body>
<main class="canvas">

  <!-- Front of card -->
  <svg class="card card-front" viewBox="0 0 770 440" xmlns="http://www.w3.org/2000/svg">
    <rect width="770" height="440" fill="var(--slate)"/>
    <g class="brand">
      <circle cx="178" cy="178" r="14" fill="var(--red)"/>
      <text class="brand-name" x="405" y="204" font-size="78" fill="var(--white)" text-anchor="middle">BRENWICK</text>
      <text class="brand-tag" x="405" y="248" font-size="22" fill="var(--white)" text-anchor="middle">CASING SERVICES</text>
    </g>
    <text class="services" x="385" y="398" text-anchor="middle">EXTERNAL CRT  |  INTERNAL CRT  |  CASING CREWS  |  TORQUE TURN  |  LAYDOWN MACHINE</text>
  </svg>

  <!-- Back of card -->
  <svg class="card card-back" viewBox="0 0 770 440" xmlns="http://www.w3.org/2000/svg">
    <rect width="770" height="440" fill="var(--white)"/>
    <path class="panel" d="M0 0 H330 C430 120 470 300 560 440 H0 Z" fill="var(--slate)"/>
    <path class="accent-curve" d="M342 0 C442 120 482 300 574 440" fill="none" stroke="var(--red)" stroke-width="3"/>

    <g class="brand">
      <circle cx="448" cy="182" r="10" fill="var(--red)"/>
      <text class="brand-name" x="610" y="200" font-size="46" fill="var(--slate)" text-anchor="middle">BRENWICK</text>
      <text class="brand-tag" x="610" y="228" font-size="15" fill="var(--slate)" text-anchor="middle" style="letter-spacing:4px">CASING SERVICES</text>
    </g>

    <g class="person">
      <text class="person-name" x="48" y="92">CODY HARLAN</text>
      <text class="person-title" x="48" y="122">AREA MANAGER</text>
      <text class="contact" x="48" y="156">Alder Springs, OK 73990</text>
    </g>

    <g class="contacts">
      <!-- office phone -->
      <path class="icon" d="M50 200 q3 -4 6 0 l3 4 q1 2 -1 4 l-2 2 q3 6 8 9 l2 -2 q2 -2 4 -1 l4 3 q3 3 0 6 l-3 2 q-8 2 -17 -9 q-8 -10 -4 -18 z"/>
      <text class="contact" x="84" y="216">(555)210-4800</text>
      <!-- cell -->
      <rect class="icon" x="55" y="230" width="14" height="22" rx="2"/>
      <rect x="58" y="233" width="8" height="13" fill="var(--slate)"/>
      <text class="contact contact-strong" x="84" y="249">(555)318-6624</text>
      <!-- fax -->
      <rect class="icon" x="51" y="271" width="22" height="11" rx="2"/>
      <rect class="icon" x="56" y="263" width="12" height="7"/>
      <rect class="icon" x="56" y="283" width="12" height="5"/>
      <text class="contact" x="84" y="282">(555)210-4815</text>
      <!-- email -->
      <rect class="icon" x="51" y="300" width="22" height="15" rx="1"/>
      <path d="M52 301 L62 309 L72 301" fill="none" stroke="var(--slate)" stroke-width="1.6"/>
      <text class="contact" x="84" y="315">cody@brenwick.com</text>
      <!-- web -->
      <circle class="icon-line" cx="62" cy="341" r="10"/>
      <ellipse class="icon-line" cx="62" cy="341" rx="4.5" ry="10"/>
      <line class="icon-line" x1="52" y1="341" x2="72" y2="341"/>
      <text class="contact" x="84" y="348">www.brenwick.com</text>
    </g>
  </svg>

</main>
</body>
</html>
```